Judicial election website to attract voters

I need a simple one-page web design for a judicial election. I'm going to put up one picture, maybe two. The picture I have needs a little touch-up (whiten teeth for example). I have 3 paragraphs of text. I'd like a "Donate" button that can link to a CoinDrift account. I'd also like a little background design, like the Constitution or something like that. There's a couple other little things but that's the bulk of it.

Target Market(s)

Involved voters and some media

Industry/Entity Type

Legal

Number of Pages Required

1 page

Font styles to use
Sans Serif

Requirements
Must have
• My picture, text, donate button
• Phrase "Remember to vote August 30, 2016!"
Nice to have
• Perhaps a second photo, maybe a short 30 second video of me talking directly to the voters, cool background: Constitution, something judgey.
Should not have
• Not sure ... profanity, I guess.

```html
<!DOCTYPE html>
<html lang="en">
<head>
<meta charset="utf-8">
<title>Civic Ballot</title>
<link href="https://fonts.googleapis.com/css2?family=Jost:wght@400;500&family=Lato:wght@400;700&display=swap" rel="stylesheet">
<style>
:root{
  --navy:#0a2463;
  --red:#c4122f;
  --text:#3b3b3b;
  --tick:#e8492c;
  --rule:#e3e3e3;
  --footer-bg:#f6f6f6;
  --bottom-bg:#323232;
}
*{margin:0;padding:0;box-sizing:border-box}
html,body{width:1200px;height:1190px;overflow:hidden;background:#fff}
body{position:relative;font-family:'Lato',sans-serif;color:var(--text)}
.brand{font-family:'Lato',sans-serif;font-weight:400;letter-spacing:1px;color:var(--navy);white-space:nowrap}
.site-header .brand{position:absolute;left:98px;top:36px;font-size:34px;line-height:1}
.donate{position:absolute;width:149px;height:46px;background:var(--navy);border-top:2px solid var(--red);border-bottom:2px solid var(--red);display:flex;align-items:center;justify-content:center;gap:10px;color:#fff;font-family:'Jost',sans-serif;font-size:20px;letter-spacing:.5px;text-decoration:none}
.site-header .donate{left:950px;top:34px}
.hero{position:absolute;left:0;top:112px;width:1200px;height:479px}
.hero-scene{position:absolute;inset:0;background:linear-gradient(90deg,#e2e4e6 0%,#eceeef 30%,#f1f2f3 55%,#dfe4ec 80%,#d6dde9 100%)}
.hero-portrait{position:absolute;right:0;top:50px;width:400px;height:429px;background:radial-gradient(ellipse at 55% 30%,#d9b9a3 0%,#cfa98a 35%,#e9896b 70%,#e58463 100%);border-radius:200px 0 0 0}
.vote-banner{position:absolute;left:98px;top:330px;width:590px;height:64px;background:var(--navy);border-left:5px solid var(--red);color:#fff;font-weight:700;font-size:31px;line-height:64px;padding-left:19px;white-space:nowrap}
.about-title{position:absolute;left:101px;top:636px;font-family:'Jost',sans-serif;font-weight:400;font-size:32px;color:var(--navy);letter-spacing:.3px}
.about-title span{color:var(--red)}
.about-rule{position:absolute;left:98px;top:683px;width:510px;height:1px;background:var(--rule)}
.about-rule::before{content:"";position:absolute;left:0;top:-1px;width:64px;height:2px;background:var(--navy)}
.about-copy{position:absolute;left:100px;top:704px;width:510px;font-size:13.7px;line-height:22px}
.about-copy p+p{margin-top:5px}
.checklist{list-style:none;margin-top:18px}
.checklist li{display:flex;align-items:center;gap:9px;height:31.5px}
.video{position:absolute;left:628px;top:685px;width:469px;height:310px;border:1px solid #cfcfcf;border-radius:6px;padding:3px;background:#fff}
.video-frame{position:relative;width:100%;height:100%;border-radius:4px;overflow:hidden}
.video-still{position:absolute;inset:0;bottom:43px;background:radial-gradient(circle at 20% 30%,#c6463a 0%,transparent 35%),radial-gradient(circle at 80% 25%,#d8a02d 0%,transparent 35%),radial-gradient(circle at 50% 60%,#f2f2f2 0%,#f0f0f0 30%,transparent 45%),linear-gradient(135deg,#3a4a6b,#7a5a4a 50%,#2e3b55)}
.play-big{position:absolute;left:50%;top:50%;transform:translate(-50%,-70%)}
.controls{position:absolute;left:0;right:0;bottom:0;height:43px;background:#111;display:flex;align-items:center;color:#fff;font-size:12px}
.controls .ctl-play{width:45px;height:43px;background:#000;display:flex;align-items:center;justify-content:center}
.controls .time{margin:0 12px 0 10px}
.track{position:relative;width:227px;height:17px;border-radius:9px;background:#3b3b3b}
.track .fill{position:absolute;left:0;top:0;bottom:0;width:100px;border-radius:9px;background:#d10b0b}
.track .knob{position:absolute;left:92px;top:0;width:17px;height:17px;border-radius:50%;background:#eee}
.controls .end{margin-left:19px;margin-right:20px}
.site-footer{position:absolute;left:0;top:1043px;width:1200px;height:104px;background:var(--footer-bg)}
.social{position:absolute;left:99px;top:43px;display:flex;gap:12px;list-style:none}
.social li{font-size:12px;font-weight:700;color:var(--navy);display:flex;align-items:center;gap:5px}
.social li::before{content:"";width:12px;height:12px;background:var(--navy)}
.site-footer .brand{position:absolute;left:490px;top:38px;font-size:27px;line-height:1}
.site-footer .donate{left:950px;top:32px}
.bottom-bar{position:absolute;left:0;top:1147px;width:1200px;height:43px;background:var(--bottom-bg);color:#f2f2f2;font-family:'Jost',sans-serif;font-size:13.5px;text-align:center;line-height:43px;letter-spacing:.2px}
</style>
</head>
<body>
<header class="site-header">
  <div class="brand">CIVIC BALLOT</div>
  <a class="donate" href="#">
    <svg width="26" height="24" viewBox="0 0 26 24" fill="none" stroke="#fff" stroke-width="2"><circle cx="17" cy="8" r="6"/><path d="M2 20h8l6-4"/><path d="M2 15h6l4 2"/></svg>
    DONATE
  </a>
</header>

<section class="hero">
  <div class="hero-scene" role="img" aria-label="Faded photo of a columned courthouse with wide steps"></div>
  <div class="hero-portrait" role="img" aria-label="Portrait photo of the candidate"></div>
  <div class="vote-banner">Remember To Vote August 30, 2016!</div>
</section>

<h2 class="about-title">ABOUT <span>ME</span></h2>
<div class="about-rule"></div>
<div class="about-copy">
  <p>Lorem ipsum dolor sit amet, consectetuer adipiscing eliett, sed diam nonummy nibh euismod tincidunt utltn laoreet dolore magna aliquam erat volutpat. Ut wisi enim ad minime veniam, quisilptqe nostrud exerci tation ullamcorper suscipit lobortis nisl ut aliquip exeaet4 commodo consequat.</p>
  <p>Lusto odio dignissim qui blandit praesent luptatum zzrileti delenit augue duis dolore teleoi feugait nulla dolor in hendrerit in vulputate consequat.</p>
  <ul class="checklist">
    <li><svg width="15" height="12" viewBox="0 0 15 12"><path d="M1.5 6l4 4 8-8.5" stroke="#e8492c" stroke-width="2.6" fill="none"/></svg>Lorem ipsum dolor sit amet, consec.</li>
    <li><svg width="15" height="12" viewBox="0 0 15 12"><path d="M1.5 6l4 4 8-8.5" stroke="#e8492c" stroke-width="2.6" fill="none"/></svg>sed diam nonummy nibh euismod tincidunt.</li>
    <li><svg width="15" height="12" viewBox="0 0 15 12"><path d="M1.5 6l4 4 8-8.5" stroke="#e8492c" stroke-width="2.6" fill="none"/></svg>Lorem ipsum dolor sit amet, consec.</li>
    <li><svg width="15" height="12" viewBox="0 0 15 12"><path d="M1.5 6l4 4 8-8.5" stroke="#e8492c" stroke-width="2.6" fill="none"/></svg>sed diam nonummy nibh euismod tincidunt.</li>
  </ul>
</div>

<div class="video">
  <div class="video-frame">
    <div class="video-still" role="img" aria-label="Video still of hands holding an election sign against colourful bokeh"></div>
    <svg class="play-big" width="56" height="56" viewBox="0 0 56 56"><circle cx="28" cy="28" r="27" fill="#fff" stroke="#ccc"/><path d="M22 16l17 12-17 12z" fill="#111"/></svg>
    <div class="controls">
      <div class="ctl-play"><svg width="14" height="16" viewBox="0 0 14 16"><path d="M1 1l12 7-12 7z" fill="#fff"/></svg></div>
      <span class="time">04:59</span>
      <div class="track"><div class="fill"></div><div class="knob"></div></div>
      <span class="end">10:35</span>
      <svg width="22" height="20" viewBox="0 0 22 20" fill="#fff"><path d="M1 7h4l6-5v16l-6-5H1z"/><path d="M14 5c3 3 3 7 0 10M17 2c5 5 5 11 0 16" stroke="#fff" stroke-width="1.8" fill="none"/></svg>
      <svg style="margin-left:16px" width="22" height="22" viewBox="0 0 22 22" stroke="#fff" stroke-width="2.4" fill="#fff"><path d="M4 4l14 14"/><path d="M2 2h7l-7 7z" stroke="none"/><path d="M20 20h-7l7-7z" stroke="none"/></svg>
    </div>
  </div>
</div>

<footer class="site-footer">
  <ul class="social">
    <li>Friendnest</li>
    <li>Chirply</li>
    <li>Linkwork</li>
    <li>Circlo</li>
  </ul>
  <div class="brand">CIVIC BALLOT</div>
  <a class="donate" href="#">
    <svg width="26" height="24" viewBox="0 0 26 24" fill="none" stroke="#fff" stroke-width="2"><circle cx="17" cy="8" r="6"/><path d="M2 20h8l6-4"/><path d="M2 15h6l4 2"/></svg>
    DONATE
  </a>
</footer>
<div class="bottom-bar">COPYRIGHT © 2016 CIVIC BALLOT. ALL RIGHTS RESERVED.</div>
</body>
</html>
```